Photography Business, Business Card

Looking for a unique cutting edge card that takes advantage of the latest printing technologies. Please review this site for all the options they office: https://glowprintly.com. If you can think it they can do it. And if you have an idea and do not know if they can do it, I will check into it.

Target Market(s)

People and places I took images of and future clients.

Industry/Entity Type

Photography

Contact Information for Business Card

Name, cell & email. Derek Holloway, dholloway@kpnvisuals.com, 312-748-2961

Colors

Designer to choose only greyscale colors for use in the design.

Requirements
Must have
• 100% cutting edge. Is so great, those I hand it to always show it to someone else. A piece of art.
Nice to have
• Blacks, silvers, greys, some red. Maybe other colors?

```html
<!DOCTYPE html>
<html lang="en">
<head>
<meta charset="utf-8">
<title>Derek Holloway Photography – Business Card</title>
<link rel="stylesheet" href="https://fonts.googleapis.com/css2?family=Montserrat:wght@300;400&display=swap">
<style>
  :root {
    --backdrop: #2f3235;
    --card-black: #0d0d0e;
    --card-edge: #1c1c1e;
    --silver-light: #e9e9ea;
    --silver-mid: #b4b5b7;
    --silver-dark: #7b7c7f;
    --text-grey: #b9babc;
  }
  * { margin: 0; padding: 0; box-sizing: border-box; }
  html, body {
    width: 1200px;
    height: 1122px;
    overflow: hidden;
    background: var(--backdrop);
    font-family: "Montserrat", sans-serif;
  }
  .canvas {
    position: relative;
    width: 1200px;
    height: 1122px;
  }
  .card {
    position: absolute;
    width: 640px;
    height: 390px;
  }
  .card--front { left: 90px; top: 70px; }
  .card--back { left: 470px; top: 600px; }
  .card-shape {
    position: absolute;
    inset: 0;
    width: 640px;
    height: 390px;
  }
  .card-shape path {
    fill: var(--card-black);
    stroke: var(--card-edge);
    stroke-width: 2;
  }
  .front-wordmark {
    position: absolute;
    left: 0;
    right: 0;
    top: 180px;
    text-align: center;
    font-size: 60px;
    font-weight: 300;
    letter-spacing: 12px;
    line-height: 1;
    color: var(--silver-mid);
    white-space: nowrap;
  }
  .studio-name {
    position: absolute;
    left: 48px;
    top: 100px;
    color: var(--text-grey);
  }
  .studio-name__person {
    font-size: 32px;
    font-weight: 300;
    letter-spacing: 1px;
    line-height: 1.1;
    white-space: nowrap;
  }
  .studio-name__trade {
    margin-top: 6px;
    font-size: 11px;
    font-weight: 400;
    letter-spacing: 5px;
    color: var(--silver-dark);
  }
  .brand-circle {
    position: absolute;
    left: 398px;
    top: 92px;
    width: 200px;
    height: 200px;
    border-radius: 50%;
    border: 6px solid var(--silver-mid);
  }
  .contact-list {
    position: absolute;
    left: 48px;
    top: 258px;
    list-style: none;
    color: var(--text-grey);
    font-size: 17px;
    font-weight: 300;
    letter-spacing: 0.5px;
  }
  .contact-list li {
    display: flex;
    align-items: center;
    gap: 12px;
    height: 30px;
    white-space: nowrap;
  }
  .contact-list svg {
    width: 14px;
    height: 14px;
    fill: var(--silver-dark);
    flex-shrink: 0;
  }
</style>
</head>
<body>
<main class="canvas">

  <section class="card card--front" aria-label="Card front">
    <svg class="card-shape" viewBox="0 0 640 390" aria-hidden="true">
      <path d="M28 30 H200 V12 H292 V2 H400 V30 H612 Q640 30 640 58 V362 Q640 390 612 390 H28 Q0 390 0 362 V58 Q0 30 28 30 Z"/>
    </svg>
    <div class="front-wordmark">HOLLOWAY</div>
  </section>

  <section class="card card--back" aria-label="Card back">
    <svg class="card-shape" viewBox="0 0 640 390" aria-hidden="true">
      <path d="M28 30 H200 V12 H292 V2 H400 V30 H612 Q640 30 640 58 V362 Q640 390 612 390 H28 Q0 390 0 362 V58 Q0 30 28 30 Z"/>
    </svg>

    <div class="studio-name">
      <div class="studio-name__person">Derek Holloway</div>
      <div class="studio-name__trade">PHOTOGRAPHY</div>
    </div>

    <div class="brand-circle" aria-hidden="true"></div>

    <ul class="contact-list">
      <li>
        <svg viewBox="0 0 14 14" aria-hidden="true"><path d="M4 0 H10 Q11.5 0 11.5 1.5 V12.5 Q11.5 14 10 14 H4 Q2.5 14 2.5 12.5 V1.5 Q2.5 0 4 0 Z M4 2 V11 H10 V2 Z" fill-rule="evenodd"/></svg>
        312-748-2961
      </li>
      <li>
        <svg viewBox="0 0 14 14" aria-hidden="true"><path d="M0 3 H14 V11 H0 Z M1 4 L7 8 L13 4 V3.6 L7 7.4 L1 3.6 Z" fill-rule="evenodd"/></svg>
        dholloway@kpnvisuals.com
      </li>
      <li>
        <svg viewBox="0 0 14 14" aria-hidden="true"><path d="M7 0 A7 7 0 1 0 7 14 A7 7 0 1 0 7 0 Z M7 1.5 A5.5 5.5 0 0 1 12.5 7 H1.5 A5.5 5.5 0 0 1 7 1.5 Z"/></svg>
        www.kpnvisuals.com
      </li>
    </ul>
  </section>

</main>
</body>
</html>
```